Tree Pruning Website

We need a website for a tree Arborist, pruning company called Maple Crest Canopy Works. We look after all types of trees, knock down trees and prune trees. Our target market is from domestic clients to government clients and everything in between.

We would like to see the use of our main colours which are orange and green

We are not looking forward in seeing a template that we have seen before but a unique template. We have designed 5 templates ourselves and we wish for the design community to take our designs to the next level.

We have also designed a template for things that **we are not** looking for (Version 4)

To make it fair for everyone, we are also not giving out any participation payments as we have had. One winner will take all of the payment!!!

I Have attached a image of the designs and a image of a tree.

We are just looking at the PSD file been developed. We have our own team who can slice the image up into a HTML format.

Target Market(s)

Everyone who needs to cut down a tree

Industry/Entity Type

Government

Requirements
Must have
• Logo on front page
A List of our services
jQuery slider on page
Phone Number on every page

```html
<!DOCTYPE html>
<html lang="en">
<head>
<meta charset="utf-8">
<title>Maple Crest Canopy Works</title>
<link href="https://fonts.googleapis.com/css2?family=Source+Sans+3:wght@400;600&display=swap" rel="stylesheet">
<style>
:root{
  --orange:#f39313;
  --orange-dark:#d97b06;
  --green:#5aaf46;
  --green-dark:#4a9a38;
  --leaf:#7cc242;
  --text:#8a8a8a;
  --heading:#444;
  --accent-red:#c8141e;
  --link-red:#9a1a1a;
  --rule:#e2e2e2;
  --footer:#2b2b2b;
  --white:#fff;
}
*{box-sizing:border-box;margin:0;padding:0}
html,body{width:1176px;height:1200px;overflow:hidden}
body{position:relative;background:var(--white);font-family:"Source Sans 3",Arial,sans-serif;color:var(--text)}
.abs{position:absolute}
.foliage-top{left:150px;top:0;width:900px;height:60px;background:linear-gradient(#dcefc8,rgba(255,255,255,0))}
.foliage-left{left:0;top:0;width:150px;height:340px;background:linear-gradient(100deg,rgba(122,190,60,.85) 0%,rgba(150,205,90,.45) 35%,rgba(255,255,255,0) 75%)}
.foliage-right{right:0;top:0;width:150px;height:340px;background:linear-gradient(260deg,rgba(122,190,60,.85) 0%,rgba(150,205,90,.45) 35%,rgba(255,255,255,0) 75%)}
.brand{left:147px;top:60px;font-size:29px;color:#555;letter-spacing:.2px}
.phone{left:794px;top:66px;display:flex;align-items:center;gap:6px;font-size:22px;color:#555}
.nav{left:111px;top:126px;width:961px;height:52px;background:var(--orange);border-radius:10px 10px 0 0;display:flex;border-bottom:1px solid var(--orange-dark)}
.nav a{color:var(--white);text-decoration:none;font-size:15.5px;display:flex;align-items:center;justify-content:center;border-right:1px solid var(--orange-dark);height:100%}
.nav a:last-child{border-right:none}
.slider{left:111px;top:178px;width:963px;height:359px;background:linear-gradient(135deg,var(--leaf),var(--green));overflow:hidden}
.slide-photo{left:12px;top:12px;width:660px;height:335px;background:linear-gradient(160deg,#8ea3b8 0%,#6f8a4a 45%,#d9d4c4 75%,#6a8a3f 100%);-webkit-mask-image:linear-gradient(90deg,#000 0%,#000 84%,transparent 100%);mask-image:linear-gradient(90deg,#000 0%,#000 84%,transparent 100%)}
.slide-title{left:650px;top:90px;font-size:23px;color:var(--white)}
.slide-text{left:650px;top:130px;width:255px;font-size:13px;line-height:21px;color:var(--white)}
.slide-btn{left:651px;top:230px;width:166px;height:44px;border-radius:8px;background:linear-gradient(#fbb431,var(--orange-dark));color:var(--white);font-size:17px;display:flex;align-items:center;justify-content:center;box-shadow:0 3px 4px rgba(0,0,0,.3)}
.slide-arrow{top:156px;width:49px;height:49px;background:var(--orange);display:flex;align-items:center;justify-content:center}
.slider-shadow{left:111px;top:537px;width:963px;height:55px;background:radial-gradient(ellipse at 50% 0,rgba(0,0,0,.16),rgba(0,0,0,0) 70%)}
.section-title{font-size:17.5px;color:var(--heading)}
.section-title em{font-style:normal;color:var(--accent-red);font-size:20px;margin-left:4px}
.rule{height:1px;background:var(--rule)}
.intro{left:125px;top:650px;width:603px;font-size:12.5px;line-height:19.6px}
.more{font-size:11.5px;color:var(--link-red)}
.thumb{top:854px;width:131px;height:122px;border:1px solid #ccc;border-radius:8px;padding:3px;box-shadow:0 1px 3px rgba(0,0,0,.2);background:var(--white)}
.thumb div{width:100%;height:100%;border-radius:6px}
.caption{top:983px;width:130px;font-size:11.5px;line-height:14px;color:#666}
.panel{left:818px;width:257px;border:1px solid #d4d4d4;border-radius:4px;background:var(--white)}
.panel-head{margin:3px;height:37px;background:var(--green);color:var(--white);font-size:17.5px;padding-left:18px;display:flex;align-items:center}
.service-list{list-style:none;padding:3px 0 0 30px}
.service-list li{font-size:12.5px;color:#555;height:23.5px;display:flex;align-items:center;gap:8px}
.testimonial-photo{left:10px;top:58px;width:78px;height:76px;border:1px solid #ddd;padding:3px}
.testimonial-photo div{width:100%;height:100%;background:linear-gradient(#dcdcdc,#b9b3ac)}
.testimonial-text{left:104px;top:55px;width:146px;font-size:11px;line-height:18px;color:#888}
.footer{left:0;top:1111px;width:1176px;height:89px;background:var(--footer);border-top:3px solid #555}
.footer-links{right:86px;top:18px;font-size:11.5px;color:#ddd}
.copyright{right:83px;top:42px;font-size:11.5px;color:#ddd}
.social{top:33px;width:24px;height:24px;border-radius:3px}
</style>
</head>
<body>

<div class="foliage-top abs" role="img" aria-label="Band of green vine leaves along the top edge"></div>
<div class="foliage-left abs" role="img" aria-label="Green vine leaves along the top left edge"></div>
<div class="foliage-right abs" role="img" aria-label="Green vine leaves along the top right edge"></div>

<div class="brand abs">Maple Crest Canopy Works</div>
<div class="phone abs">
  <svg width="24" height="30" viewBox="0 0 24 30"><path d="M6 2l5 6-3 3c1 4 4 8 8 10l3-3 5 5-4 5C10 27 1 15 3 5z" fill="#666"/></svg>
  <span>555 0148 2270</span>
</div>

<nav class="nav abs">
  <a href="#" style="width:123px">Home</a>
  <a href="#" style="width:130px">About Us</a>
  <a href="#" style="width:150px">Our Services</a>
  <a href="#" style="width:154px">Get &nbsp;a Quote</a>
  <a href="#" style="width:147px">Contact Us</a>
</nav>

<section class="slider abs">
  <div class="slide-photo abs" role="img" aria-label="Looking up into a tall white-barked gum tree canopy"></div>
  <div class="slide-arrow abs" style="left:12px">
    <svg width="12" height="18" viewBox="0 0 12 18"><path d="M10 1L2 9l8 8" stroke="#8a4a00" stroke-width="2.5" fill="none"/></svg>
  </div>
  <div class="slide-arrow abs" style="left:913px">
    <svg width="12" height="18" viewBox="0 0 12 18"><path d="M2 1l8 8-8 8" stroke="#3f8c2e" stroke-width="2.5" fill="none"/></svg>
  </div>
  <h2 class="slide-title abs" style="font-weight:400">TREE PRUNING</h2>
  <p class="slide-text abs">Uenim ad minim veniam, quis nostrud nisi laboris utaliquip ex irurdolor into Uenim ad minim veniam, quis nostrud nisi laboris utaliquip ex irurdolor into</p>
  <div class="slide-btn abs">LEARN MORE &gt;&gt;</div>
</section>
<div class="slider-shadow abs"></div>

<h2 class="section-title abs" style="left:123px;top:612px;font-weight:400">Welcome to <em>Maple Crest Canopy Works</em></h2>
<div class="rule abs" style="left:123px;top:640px;width:604px"></div>
<p class="intro abs">Sed ut perspiciatis unde omnis iste natus error sit voluptatem accusantium doloremque laudantium, totam rem aperiam, eaque ipsa quae ab illo inventore veritatis et quasi architecto beatae vitae dicta sunt explicabo. Nemo enim ipsam voluptatem quia voluptas sit aspernatur aut odit aut fugit, sed quia consequuntur magni dolores eos qui ratione voluptatem sequi nesciunt. Neque porro quisquam est, qui dolorem ipsum quia dolor sit amet, con-sectetur, adipisci velit, sed quia non numquam eius modi tempora incidunt ut labore et dolore magnam aliquam quaerat voluptatem aliquid ex ea commodi consequatur.</p>
<span class="more abs" style="left:679px;top:773px">MORE &gt;&gt;</span>

<h2 class="section-title abs" style="left:123px;top:812px;font-weight:400">Photo Gallery</h2>
<div class="rule abs" style="left:123px;top:836px;width:604px"></div>

<div class="thumb abs" style="left:123px"><div role="img" aria-label="Arborist climbing among green foliage" style="background:linear-gradient(#3f7a2a,#6aa640)"></div></div>
<div class="thumb abs" style="left:284px"><div role="img" aria-label="Climber pruning bare branches against blue sky" style="background:linear-gradient(#4f7fc4,#8aa7cf)"></div></div>
<div class="thumb abs" style="left:446px"><div role="img" aria-label="Large rounded green tree under blue sky" style="background:linear-gradient(#5d8fd0,#3f8a2c 60%,#5c8d3a)"></div></div>
<div class="thumb abs" style="left:608px"><div role="img" aria-label="Tree trunk viewed from below with green canopy" style="background:linear-gradient(#7fae4f,#5c6f3a)"></div></div>

<p class="caption abs" style="left:128px">Sed ut perspiciatis unde omnis iste natus error sit voluptatem laudantium.</p>
<p class="caption abs" style="left:289px">Sed ut perspiciatis unde omnis iste natus error sit voluptatem laudantium.</p>
<p class="caption abs" style="left:451px">Sed ut perspiciatis unde omnis iste natus error sit voluptatem laudantium.</p>
<p class="caption abs" style="left:613px">Sed ut perspiciatis unde omnis iste natus error sit voluptatem laudantium.</p>
<span class="more abs" style="left:128px;top:1032px">MORE &gt;&gt;</span>
<span class="more abs" style="left:289px;top:1032px">MORE &gt;&gt;</span>
<span class="more abs" style="left:451px;top:1032px">MORE &gt;&gt;</span>
<span class="more abs" style="left:613px;top:1032px">MORE &gt;&gt;</span>

<aside class="panel abs" style="top:607px;height:256px">
  <div class="panel-head">Our Services</div>
  <ul class="service-list">
    <li><svg width="11" height="11" viewBox="0 0 11 11"><path d="M1 5.5h6M4.5 3l2.5 2.5L4.5 8M8 1h2v9H8" stroke="var(--orange)" stroke-width="1.3" fill="none"/></svg>Diagnosis</li>
    <li><svg width="11" height="11" viewBox="0 0 11 11"><path d="M1 5.5h6M4.5 3l2.5 2.5L4.5 8M8 1h2v9H8" stroke="var(--orange)" stroke-width="1.3" fill="none"/></svg>Treatment</li>
    <li><svg width="11" height="11" viewBox="0 0 11 11"><path d="M1 5.5h6M4.5 3l2.5 2.5L4.5 8M8 1h2v9H8" stroke="var(--orange)" stroke-width="1.3" fill="none"/></svg>Pruning</li>
    <li><svg width="11" height="11" viewBox="0 0 11 11"><path d="M1 5.5h6M4.5 3l2.5 2.5L4.5 8M8 1h2v9H8" stroke="var(--orange)" stroke-width="1.3" fill="none"/></svg>Tree Removal</li>
    <li><svg width="11" height="11" viewBox="0 0 11 11"><path d="M1 5.5h6M4.5 3l2.5 2.5L4.5 8M8 1h2v9H8" stroke="var(--orange)" stroke-width="1.3" fill="none"/></svg>Stump Removal</li>
    <li><svg width="11" height="11" viewBox="0 0 11 11"><path d="M1 5.5h6M4.5 3l2.5 2.5L4.5 8M8 1h2v9H8" stroke="var(--orange)" stroke-width="1.3" fill="none"/></svg>Cabling &amp; Bracing</li>
    <li><svg width="11" height="11" viewBox="0 0 11 11"><path d="M1 5.5h6M4.5 3l2.5 2.5L4.5 8M8 1h2v9H8" stroke="var(--orange)" stroke-width="1.3" fill="none"/></svg>Arborist Consults</li>
    <li><svg width="11" height="11" viewBox="0 0 11 11"><path d="M1 5.5h6M4.5 3l2.5 2.5L4.5 8M8 1h2v9H8" stroke="var(--orange)" stroke-width="1.3" fill="none"/></svg>Tree Protection</li>
  </ul>
</aside>

<aside class="panel abs" style="top:892px;height:197px">
  <div class="panel-head">Testimonials</div>
  <div class="testimonial-photo abs"><div role="img" aria-label="Portrait photo of the client"></div></div>
  <p class="testimonial-text abs">Nunc varius facilisis eros.<br>Sed erat. In in velit quis arcu ornare laoreet. luctus &nbsp;massa ornare laoreet. luctus &nbsp;massa. Nunc varius facilisis eros.</p>
  <span class="abs" style="left:103px;top:151px;font-size:11px;color:var(--link-red)">Daniel Hartwell</span>
  <span class="more abs" style="left:187px;top:175px">MORE &gt;&gt;</span>
</aside>

<footer class="footer abs">
  <div class="social abs" style="left:117px;background:#3b5a98"></div>
  <div class="social abs" style="left:154px;background:#3aa3d8"></div>
  <div class="social abs" style="left:191px;background:#1f6aa8"></div>
  <div class="social abs" style="left:228px;background:#f08a1c"></div>
  <div class="footer-links abs">Privacy Policy &nbsp;| &nbsp;Terms of Use</div>
  <div class="copyright abs">© 2013 MCCW, All Rights Reserved</div>
</footer>

</body>
</html>
```